NEW Household Invention Needs a Package Design!

We need a 'retail' package design for a new product invented for the household kitchen market. Trimbolt has developed a reusable food storage system that can be tailored to an individual's needs and have a sustainable impact on their ability to make good dietary decisions, while helping save the planet. We would like to see designs that use the brand's branding guidelines and logo. The final design should communicate the key features of the product (patented customizable modular system, fill lines, collapsible functionality and sustainable materials), as well as, all other notable aspects (Microwave/Dishwasher Safe, Leakproof, 100% BPA Free, Donates 1% of purchase price, etc.). It's important that the benefits of the product are well highlighted (More variety to better balance nutrition, More easily stored in bag, kitchen cabinet or drawer and Ends waste)
Updates

Hi All, we are looking for a package design for retail, something that will be on a shelf in our product category.

Target Market(s)

Health conscious men and women who have a passion for nutrition & social responsibility, operate a lifestyle on-the-go and monitor their spending by preparing meals at home.

Industry/Entity Type

Food Tech, Consumer Products, Health & Wellness

Font styles to use
Other font styles liked:
• See Brand Guidelines

Requirements
Must have
• Follow brand guidelines: https://guidelines.korvepixel.example/trimbolt/guidelines/

```html
<!DOCTYPE html>
<html lang="en">
<head>
<meta charset="utf-8">
<title>Trimbolt – Reusable Food Storage System package</title>
<link rel="stylesheet" href="https://fonts.googleapis.com/css2?family=Barlow:wght@500;600&family=Barlow+Condensed:wght@400;500;600&family=Caveat+Brush&family=Poppins:wght@500&display=swap">
<style>
  :root{
    --backdrop:#d3e3ea;
    --plum:#7a1c55;
    --coral:#f0524b;
    --blush:#e9c3d1;
    --blush-soft:#efd6df;
    --cream:#f2ece7;
    --ink:#1d1a1c;
    --sky:#8fc6e6;
  }
  *{box-sizing:border-box;margin:0;padding:0}
  html,body{width:1200px;height:1056px;overflow:hidden}
  body{background:var(--backdrop);position:relative;font-family:"Barlow",Arial,sans-serif;color:var(--ink)}

  .panel{position:absolute;top:178px;width:560px;height:700px;overflow:hidden;
    background:linear-gradient(180deg,var(--blush) 0%,var(--blush-soft) 55%,var(--cream) 78%,var(--cream) 100%)}
  .panel::before,.panel::after{content:"";position:absolute;left:0;right:0;height:12px;background:var(--plum)}
  .panel::before{top:0}
  .panel::after{bottom:0}
  .panel--side{left:30px}
  .panel--front{left:610px}

  .brand-name{position:absolute;font-family:"Poppins",sans-serif;font-weight:500;color:var(--coral);letter-spacing:.5px;line-height:1}
  .panel--front .brand-name{top:50px;left:0;right:0;text-align:center;font-size:54px}
  .panel--side .brand-name{top:40px;left:40px;font-size:38px}

  .product-title{position:absolute;font-family:"Caveat Brush",cursive;font-weight:400;color:var(--plum);text-transform:uppercase;line-height:.92;white-space:nowrap;
    text-shadow:2px 0 0 var(--coral),-2px 0 0 var(--coral),0 2px 0 var(--coral),0 -2px 0 var(--coral),2px 2px 0 var(--coral),-2px -2px 0 var(--coral),2px -2px 0 var(--coral),-2px 2px 0 var(--coral)}
  .panel--front .product-title{top:122px;left:0;right:0;text-align:center;font-size:76px}
  .panel--side .product-title{top:92px;left:30px;font-size:60px}

  .hero-art{position:absolute;left:150px;top:330px;width:270px;height:255px;border-radius:18px;
    background:linear-gradient(180deg,#aad3ec 0%,var(--sky) 55%,#e6c0c4 100%)}

  .callout{position:absolute;font-family:"Barlow",sans-serif;font-weight:600;font-size:14px;line-height:1.15;color:var(--ink)}
  .callout--modular{left:10px;top:350px;width:130px;text-align:center}
  .callout--fill{left:28px;top:452px}
  .callout--collapse{left:440px;top:300px}
  .callout--materials{left:440px;top:352px}
  .callout-arrows{position:absolute;left:0;top:0;width:560px;height:700px;pointer-events:none}

  .feature-row{position:absolute;left:50px;right:50px;top:600px;height:80px}
  .feature-row svg{position:absolute;left:0;top:0}
  .feature{position:absolute;top:0;width:130px;text-align:center}
  .feature__label{display:block;margin-top:58px;font-family:"Barlow Condensed",sans-serif;font-weight:600;font-size:10.5px;white-space:nowrap;color:var(--ink)}

  .globe-art{position:absolute;left:-70px;top:310px;width:230px;height:370px;border-radius:50% 50% 40% 40%;
    background:linear-gradient(160deg,#2f6b43 0%,#7eb0d4 45%,#3a7a4f 70%,#c9a36b 100%)}
  .side-copy{position:absolute;left:190px;top:330px;width:330px;font-family:"Barlow Condensed",sans-serif;font-size:12.5px;line-height:1.35}
  .side-copy h2{font-size:17px;font-weight:600;color:var(--plum);margin-bottom:4px}
  .side-copy ul{list-style:none;margin-bottom:16px}
  .side-copy li::before{content:"• "}
  .side-copy h3{font-size:15px;font-weight:600;color:var(--coral);margin-bottom:3px}
  .side-copy p{text-align:justify;margin-bottom:16px}
  .side-copy .web-address{font-size:15px;font-weight:600;color:var(--plum);text-decoration:none}
</style>
</head>
<body>

<section class="panel panel--side" aria-label="Side panel">
  <div class="brand-name">Trimbolt</div>
  <h1 class="product-title">Reusable Food<br>Storage System</h1>
  <div class="globe-art" role="img" aria-label="Illustration of the Earth surrounded by fresh vegetables and a packed lunch container"></div>
  <div class="side-copy">
    <h2>Benefits of the product</h2>
    <ul>
      <li>More variety to better balance nutrition</li>
      <li>More easily stored in bag</li>
      <li>Kitchen cabinet or drawer and Ends waste</li>
    </ul>
    <h3>What is Lorem Ipsum?</h3>
    <p>Lorem Ipsum is simply dummy text of the printing and typesetting industry. Lorem Ipsum has been the industry's standard dummy text ever since the 1500s, when an unknown printer took a galley of type and scrambled it to make a type specimen book. It has survived not only five centuries, but also the leap into electronic typesetting, remaining essentially unchanged. It was popularised in the 1960s with the release of Dryprint sheets containing Lorem Ipsum passages, and more recently with desktop publishing software like Corvo PageSetter including versions of Lorem Ipsum.</p>
    <a class="web-address" href="#">www.trimbolt.example</a>
  </div>
</section>

<section class="panel panel--front" aria-label="Front panel">
  <div class="brand-name">Trimbolt</div>
  <h1 class="product-title">Reusable Food<br>Storage System</h1>

  <div class="hero-art" role="img" aria-label="Illustration of blue collapsible food containers with lids, a fork and spoon, surrounded by watermelon, avocado, potatoes, peppers, mushrooms and greens"></div>

  <svg class="callout-arrows" viewBox="0 0 560 700" aria-hidden="true">
    <g fill="none" stroke="#ffffff" stroke-width="2" stroke-linecap="round">
      <path d="M95 336 C125 322 150 326 168 346"/><path d="M160 343 L168 346 L168 337"/>
      <path d="M95 448 C120 436 145 440 160 458"/><path d="M152 455 L160 458 L161 450"/>
      <path d="M434 308 C412 304 398 316 390 334"/><path d="M387 325 L390 334 L398 330"/>
      <path d="M434 360 C416 356 404 366 398 382"/><path d="M395 373 L398 382 L406 378"/>
    </g>
  </svg>
  <div class="callout callout--modular">Patented customizable modular system</div>
  <div class="callout callout--fill">Fill Lines</div>
  <div class="callout callout--collapse">Collapsible<br>Functionality</div>
  <div class="callout callout--materials">Sustainable<br>Materials</div>

  <div class="feature-row">
    <svg width="460" height="60" viewBox="0 0 460 60" aria-hidden="true">
      <path d="M52 50 C80 50 80 10 110 10 M170 50 C200 50 200 10 230 10 M290 50 C320 50 320 10 350 10" fill="none" stroke="#f0524b" stroke-width="1.2"/>
      <g fill="#f0524b">
        <circle cx="55" cy="28" r="26"/><circle cx="175" cy="28" r="26"/>
        <circle cx="295" cy="28" r="26"/><circle cx="415" cy="28" r="26"/>
      </g>
      <g fill="none" stroke="#ffffff" stroke-width="2.2" stroke-linecap="round">
        <circle cx="50" cy="34" r="7"/><circle cx="61" cy="34" r="7"/>
        <path d="M42 22 L50 14 M48 22 L56 14 M54 22 L62 14 M60 22 L68 14"/>
        <path d="M175 15 C168 25 165 30 165 34 A10 10 0 0 0 185 34 C185 30 182 25 175 15 Z"/>
        <circle cx="175" cy="28" r="17"/><path d="M163 16 L187 40"/>
        <path d="M287 34 C287 22 300 18 304 16 C304 28 298 34 287 34 Z"/>
        <path d="M405 38 L420 38 L428 32 M402 42 L412 30 L422 30"/>
        <circle cx="418" cy="19" r="7"/>
      </g>
    </svg>
    <div class="feature" style="left:-10px"><span class="feature__label">Microwave/Dishwasher Safe</span></div>
    <div class="feature" style="left:110px"><span class="feature__label">Leakproof</span></div>
    <div class="feature" style="left:230px"><span class="feature__label">100% BPA Free</span></div>
    <div class="feature" style="left:350px"><span class="feature__label">Donates 1% of purchase price</span></div>
  </div>
</section>

</body>
</html>
```